New Webpage for High Class Expert Witness Services Company

We are looking for a minimalist design for a webpage that just has our logo and an entry form offer to connect with one of our Liaisons.
The entry form should just ask for Name, Email, Contact Info and Description of Project.

Company Name is: The Marlowe Crest Advisory Services

Number of Pages Required

1 page

```html
<!DOCTYPE html>
<html lang="en">
<head>
<meta charset="utf-8">
<title>Marlowe Crest Advisory Services</title>
<link rel="stylesheet" href="https://fonts.googleapis.com/css2?family=Cinzel:wght@400;600&family=Manrope:wght@400&family=Roboto:wght@400&display=swap">
<style>
:root{
  --bg:#000;
  --ink:#ffffff;
  --ink-soft:#d9d9d9;
  --ink-muted:#a9a9a9;
  --silver:#c9c9c9;
  --headline-dim:#9c9c9c;
  --panel:rgba(22,22,22,.72);
  --panel-line:#3a3a3a;
  --field-line:#bdbdbd;
  --footer-line:#3c3c3c;
  --footer-ink:#9a9a9a;
  --button-a:#e6e6e8;
  --button-b:#9d9da1;
  --button-ink:#111;
}
*{box-sizing:border-box;margin:0;padding:0}
html,body{width:1200px;height:741px;overflow:hidden;background:var(--bg)}
.page{position:relative;width:1200px;height:741px;overflow:hidden;background:var(--bg);font-family:"Roboto",Arial,sans-serif;color:var(--ink)}
.mesh-backdrop{position:absolute;left:0;top:170px;width:1200px;height:500px;
  background:
    radial-gradient(ellipse 60% 30% at 35% 70%,rgba(120,120,120,.22),transparent 70%),
    radial-gradient(ellipse 50% 25% at 85% 45%,rgba(110,110,110,.18),transparent 70%),
    linear-gradient(180deg,transparent 0%,rgba(70,70,70,.14) 45%,rgba(40,40,40,.12) 75%,transparent 100%);}
.brand{position:absolute;left:141px;top:64px;display:flex;align-items:center;gap:14px}
.brand-mark{width:46px;height:62px;background:var(--silver)}
.brand-name{font-family:"Cinzel",Georgia,serif;font-weight:400;color:var(--silver);line-height:1}
.brand-name .line-1{display:block;font-size:31px;letter-spacing:.5px}
.brand-name .line-2{display:block;font-size:15.5px;letter-spacing:5px;margin-top:6px}
.brand-name .line-3{display:block;font-size:9px;letter-spacing:3.2px;margin-top:7px}
.hero{position:absolute;left:141px;top:238px;width:500px}
.hero-title{font-family:"Cinzel",Georgia,serif;font-weight:400;font-size:44px;line-height:51px;color:var(--ink-soft);letter-spacing:.3px}
.hero-title .dim{color:var(--headline-dim)}
.hero-text{margin-top:16px;font-family:"Manrope",Arial,sans-serif;font-size:14.3px;line-height:28px;color:var(--ink-soft);width:480px;padding-left:3px}
.connect{position:absolute;left:716px;top:123px;width:378px;height:437px;background:var(--panel);border:1px solid var(--panel-line);padding:36px 36px 0 45px}
.connect-title{font-family:"Cinzel",Georgia,serif;font-weight:400;font-size:24px;letter-spacing:.2px;color:var(--ink);line-height:1}
.connect-form{margin-top:26px;display:flex;flex-direction:column;gap:12px;width:296px}
.field{display:block;width:294px;height:42px;border:1px solid var(--field-line);background:rgba(0,0,0,.55);color:var(--ink);font:400 13px/1 "Roboto",Arial,sans-serif;padding:0 17px;outline:none}
.field::placeholder{color:var(--ink)}
.field-area{height:89px;padding-top:13px;resize:none}
.submit{margin-top:1px;width:297px;height:44px;border:0;background:linear-gradient(100deg,var(--button-a) 0%,var(--button-a) 45%,var(--button-b) 100%);color:var(--button-ink);font:600 15px/1 "Cinzel",Georgia,serif;letter-spacing:.5px}
.site-footer{position:absolute;left:0;top:679px;width:1200px;border-top:1px solid var(--footer-line);text-align:center;padding-top:22px;font-size:12.4px;color:var(--footer-ink)}
</style>
</head>
<body>
<div class="page">
  <div class="mesh-backdrop" role="img" aria-label="Dark backdrop of a glowing hexagonal network mesh"></div>

  <header class="brand">
    <span class="brand-mark"></span>
    <div class="brand-name">
      <span class="line-1">MARLOWE CREST</span>
      <span class="line-2">ADVISORY SERVICES</span>
      <span class="line-3">SEAMLESS MEDICAL EXPERT INTEGRATION</span>
    </div>
  </header>

  <section class="hero">
    <h1 class="hero-title"><span class="dim">SEAMLESS</span> MEDICAL<br><span class="dim">EXPERT</span> INTEGRATION</h1>
    <p class="hero-text">Lorem ipsum dolor sit amet, consectetur adipiscing elit, sed do eiusmod tempor incididunt ut labore et dolore magna aliqua.</p>
  </section>

  <aside class="connect">
    <h2 class="connect-title">CONNECT WITH US</h2>
    <form class="connect-form">
      <input class="field" type="text" placeholder="Name*">
      <input class="field" type="email" placeholder="Email*">
      <input class="field" type="tel" placeholder="Phone number*">
      <textarea class="field field-area" placeholder="Description of Project"></textarea>
      <button class="submit" type="button">SUBMIT</button>
    </form>
  </aside>

  <footer class="site-footer">© 2026 Marlowe Crest Advisory Services. All Rights Reserved</footer>
</div>
</body>
</html>
```